Ridgeline Orchards Organic Cherry POS card 7x11

We are wanting to create a one-sided 7 x 11 organic cherry card that is eye catching and informative.This should be clear and easy to read and not cluttered. We use these cards as a display in grocery stores, demo stands, and other events to market Organic Ridgeline Sweet Orchards. We have a few facts that we would like displayed on the card (see attachment).

Target Market(s)

Consumers

Industry/Entity Type

Agriculture

Requirements
Must have
• Natural color palettes
• Easy to read
• Ridgeline Orchards
Nice to have
• Unique, realistic cherry design

```html
<!DOCTYPE html>
<html lang="en">
<head>
<meta charset="utf-8">
<title>Ridgeline Orchards – Organic Cherry Card</title>
<link rel="stylesheet" href="https://fonts.googleapis.com/css2?family=Josefin+Sans:wght@300;400&family=Dancing+Script:wght@700&display=swap">
<style>
  :root {
    --page: #ffffff;
    --bg-top: #8a7463;
    --bg-mid: #6e4b45;
    --bg-low: #5a3136;
    --photo-tone: rgba(92, 18, 32, 0.85);
    --photo-edge: rgba(92, 18, 32, 0);
    --ink: rgba(236, 224, 220, 0.88);
    --ink-white: #ffffff;
    --frame: rgba(225, 210, 205, 0.7);
    --ring: rgba(255, 255, 255, 0.55);
  }
  * { margin: 0; padding: 0; box-sizing: border-box; }
  html, body { width: 1200px; height: 880px; overflow: hidden; background: var(--page); }
  .canvas { position: relative; width: 1200px; height: 880px; background: var(--page); }
  .card {
    position: absolute; left: 0; top: 58px; width: 1200px; height: 764px; overflow: hidden;
    background:
      radial-gradient(ellipse 380px 260px at 220px 140px, rgba(190,160,130,0.35), transparent 70%),
      linear-gradient(180deg, var(--bg-top) 0%, var(--bg-mid) 45%, var(--bg-low) 100%);
  }
  .cherry-photo {
    position: absolute; left: 560px; top: 0; width: 640px; height: 764px;
    background: radial-gradient(ellipse 340px 300px at 55% 60%, var(--photo-tone) 0%, var(--photo-edge) 100%);
  }
  .brand {
    position: absolute; left: 0; width: 1200px; top: 56px; text-align: center;
    font-family: "Josefin Sans", sans-serif; font-weight: 300; font-size: 40px;
    letter-spacing: 0.08em; color: var(--ink-white);
  }
  .brand-dot {
    display: inline-block; width: 30px; height: 30px; border: 2px solid var(--ink-white);
    border-radius: 50%; vertical-align: -4px; margin-right: 16px;
  }
  .frame { position: absolute; left: 0; top: 0; }
  .facts {
    position: absolute; left: 52px; top: 0;
    font-family: "Josefin Sans", sans-serif; font-weight: 400; font-size: 33px;
    letter-spacing: 0.3em; color: var(--ink); text-transform: uppercase;
  }
  .facts span { position: absolute; left: 0; white-space: nowrap; line-height: 1; }
  .benefits {
    position: absolute; left: 0; top: 0;
    font-family: "Dancing Script", cursive; font-weight: 700; font-size: 25px; color: var(--ink-white);
  }
  .benefits span { position: absolute; white-space: nowrap; transform: translateX(-50%); line-height: 1; }
</style>
</head>
<body>
<div class="canvas">
  <div class="card">
    <div class="cherry-photo" role="img" aria-label="Photograph of two ripe dark red cherries with water droplets hanging from green stems"></div>

    <div class="brand"><span class="brand-dot"></span>Ridgeline Orchards</div>

    <svg class="frame" width="1200" height="764" viewBox="0 0 1200 764" aria-hidden="true">
      <rect x="22" y="162" width="1156" height="556" fill="none" stroke="var(--frame)" stroke-width="3" stroke-dasharray="22 14"/>
      <circle cx="920" cy="550" r="146" fill="none" stroke="var(--ring)" stroke-width="3"/>
    </svg>

    <div class="facts">
      <span style="top:200px">Organic</span>
      <span style="top:244px">Ridgeline Cherries</span>
      <span style="top:302px">Make up 1/3</span>
      <span style="top:360px">of the nation's</span>
      <span style="top:404px">production.</span>
      <span style="top:466px">Washington State</span>
      <span style="top:510px">is the nation's</span>
      <span style="top:554px">largest producer</span>
      <span style="top:598px">&nbsp;of organic</span>
      <span style="top:640px">cherries.</span>
    </div>

    <div class="benefits">
      <span style="left:928px;top:414px">Health benefits:</span>
      <span style="left:928px;top:458px">fat free</span>
      <span style="left:884px;top:498px">source of vitamin C</span>
      <span style="left:896px;top:542px">a natural anti-inflammatory</span>
      <span style="left:936px;top:586px">source of potassium</span>
      <span style="left:908px;top:630px">source of melatonin</span>
    </div>
  </div>
</div>
</body>
</html>
```